Business card for Bio pharmaceutical company

Hello,
We are a bio pharmaceutical contract manufacturing company in Brisbane, Australia. Can you please create a new business card design. Please go to our website for colours http://www.corvalinbio.com.au.
On the back can you include the cartoon mascot Tobi Tumlo and the tagline
"A Global Biopharmaceutical Contract Development Manufacturing Company"
Target Market(s)
Biotechnology
Industry/Entity Type
Pharmaceutical
Contact Information for Business Card
Maren Holtby
Business Development Manager
maren.holtby@corvalinbio.com.au
1947 Kestrel Road Marlow Queesnland 4183 Australia
T: +61 7 3951 4820
M +61 415 206 718
F +61 7 3842 6093
www.corvalinbio.com.au

```html
<!DOCTYPE html>
<html lang="en">
<head>
<meta charset="utf-8">
<title>Corvalin Bio – Business Card</title>
<link rel="stylesheet" href="https://fonts.googleapis.com/css2?family=Questrial&display=swap">
<style>
  :root {
    --page-bg: #e9ebed;
    --card-white: #ffffff;
    --card-mist: #e6e8ea;
    --brand-navy: #1b5878;
    --brand-lime: #b7d13c;
    --text-light: #ffffff;
  }
  * { box-sizing: border-box; margin: 0; padding: 0; }
  html, body {
    width: 1200px;
    height: 900px;
    overflow: hidden;
    background: var(--page-bg);
    font-family: "Questrial", "Century Gothic", sans-serif;
  }
  .business-card {
    position: absolute;
    left: 120px;
    top: 170px;
    width: 960px;
    height: 560px;
    border-radius: 40px;
    overflow: hidden;
    background: radial-gradient(ellipse at 30% 30%, var(--card-white) 40%, var(--card-mist) 100%);
    box-shadow: 0 10px 30px rgba(0,0,0,0.15);
  }
  .card-waves {
    position: absolute;
    inset: 0;
    width: 100%;
    height: 100%;
  }
  .brand-wordmark {
    position: absolute;
    left: 70px;
    top: 90px;
    display: flex;
    align-items: center;
    gap: 18px;
    font-size: 74px;
    letter-spacing: -1px;
    color: var(--brand-navy);
  }
  .brand-square {
    width: 34px;
    height: 34px;
    background: var(--brand-lime);
  }
  .contact-block {
    position: absolute;
    right: 48px;
    top: 258px;
    text-align: right;
    color: var(--text-light);
  }
  .person-name {
    font-size: 24px;
    font-weight: 400;
    letter-spacing: 1px;
    text-transform: uppercase;
    line-height: 1.2;
  }
  .person-title {
    font-size: 13px;
    letter-spacing: 1.5px;
    text-transform: uppercase;
    margin-top: 2px;
    margin-bottom: 16px;
  }
  .contact-list { list-style: none; }
  .contact-item {
    display: flex;
    justify-content: flex-end;
    align-items: center;
    gap: 12px;
    font-size: 18px;
    height: 32px;
  }
  .contact-icon {
    width: 20px;
    height: 20px;
    flex: none;
  }
  .office-address {
    position: absolute;
    right: 80px;
    bottom: 26px;
    color: var(--text-light);
    font-size: 20px;
    letter-spacing: 0.5px;
  }
</style>
</head>
<body>
  <article class="business-card">
    <svg class="card-waves" viewBox="0 0 960 560" preserveAspectRatio="none" aria-hidden="true">
      <path fill="var(--brand-lime)" d="M0,292 C150,416 300,426 460,340 C600,262 760,180 960,160 L960,560 L0,560 Z"/>
      <path fill="var(--card-white)" d="M0,316 C150,432 300,440 460,356 C600,278 760,192 960,170 L960,560 L0,560 Z"/>
      <path fill="var(--brand-navy)" d="M0,330 C150,444 300,452 460,368 C600,290 760,202 960,178 L960,560 L0,560 Z"/>
    </svg>

    <div class="brand-wordmark">
      <span class="brand-name">Corvalin Bio</span>
      <span class="brand-square"></span>
    </div>

    <section class="contact-block">
      <h1 class="person-name">Maren Holtby</h1>
      <p class="person-title">Business Development Manager</p>
      <ul class="contact-list">
        <li class="contact-item">
          <span>T: +61 7 3951 4820</span>
          <svg class="contact-icon" viewBox="0 0 24 24" fill="white"><path d="M6.6 10.8a15 15 0 0 0 6.6 6.6l2.2-2.2a1 1 0 0 1 1-.25 11.4 11.4 0 0 0 3.6.57 1 1 0 0 1 1 1V20a1 1 0 0 1-1 1A17 17 0 0 1 3 4a1 1 0 0 1 1-1h3.5a1 1 0 0 1 1 1c0 1.25.2 2.45.57 3.57a1 1 0 0 1-.25 1z"/></svg>
        </li>
        <li class="contact-item">
          <span>M: +61 415 206 718</span>
          <svg class="contact-icon" viewBox="0 0 24 24" fill="none" stroke="white" stroke-width="2"><rect x="7" y="2" width="10" height="20" rx="2"/><line x1="11" y1="18" x2="13" y2="18"/></svg>
        </li>
        <li class="contact-item">
          <span>F: +61 7 3842 6093</span>
          <svg class="contact-icon" viewBox="0 0 24 24" fill="white"><rect x="7" y="3" width="10" height="6"/><rect x="3" y="10" width="18" height="9" rx="1"/><rect x="7" y="15" width="10" height="6" fill="var(--brand-navy)" stroke="white" stroke-width="1.5"/></svg>
        </li>
        <li class="contact-item">
          <span>maren.holtby@corvalinbio.com.au</span>
          <svg class="contact-icon" viewBox="0 0 24 24" fill="white"><path d="M2 5h20v14H2z"/><path d="M2 5l10 8 10-8" fill="none" stroke="var(--brand-navy)" stroke-width="1.8"/></svg>
        </li>
        <li class="contact-item">
          <span>www.corvalinbio.com.au</span>
          <svg class="contact-icon" viewBox="0 0 24 24" fill="none" stroke="white" stroke-width="1.8"><circle cx="12" cy="12" r="9"/><ellipse cx="12" cy="12" rx="4" ry="9"/><line x1="3" y1="12" x2="21" y2="12"/></svg>
        </li>
      </ul>
    </section>

    <p class="office-address">1947 Kestrel Road Marlow Queesnland 4183 Australia</p>
  </article>
</body>
</html>
```